Anzeigengestaltung für einen einen ambulanten Pflegedienst
Zielgruppe
Insgesamt möchte ich gern drei Anzeigen für das Internet gestalten haben. Ich betreibe einen ambulanten Pflegedienst. Die erste Anzeige soll dazu dienen Kunden anzusprechen, die einen Unterstützungsbedarf und / oder einen Beratungsbedarf haben. Die zweite Anzeige soll dazu dienen neues Personal anzuwerben. Die dritte Anzeige soll speziell potenzielle Azubis ansprechen. Die Anzeigen sind gedacht für Tralvio und Pexumora hauptsächlich. In den Druck sollte es schon 10cm x 8cm sein. Es wäre super wenn vielleicht auch eine Art Aufruf an ehrenamtliche Mitarbeiter erfolgt.
Aufgabenstellung
Die Anzeigen sollen den Stil der Homepage beibehalten. Freundlich, frisch und agil wirken. Alle sollten emotional ansprechend sein und gerade der für zukünftige Mitarbeiter sollte deutlich ein gutes Betriebsklima vermitteln. Als Datei habe ich einige Bilder, die bereits für die Homepage oder Flyer verwendet wurden hochgeladen. des Weiteren habe ich die einzelnen Seiten des Flyers hochgeladen.

```html
<!DOCTYPE html>
<html lang="de">
<head>
<meta charset="utf-8">
<title>Stellenanzeige – Komm in unser Team Pflege</title>
<link href="https://fonts.googleapis.com/css2?family=Playfair+Display:wght@400&family=Quicksand:wght@500;600;700&display=swap" rel="stylesheet">
<style>
  :root {
    --teal: #47aea9;
    --green: #7aad3a;
    --ink: #555558;
    --band: #e1f1f9;
    --white: #ffffff;
    --ring: #ecece8;
  }
  html, body { margin: 0; padding: 0; overflow: hidden; }
  body { width: 1200px; height: 960px; background: var(--white); }
  .ad {
    position: relative; width: 1200px; height: 960px; overflow: hidden;
    background: var(--white); font-family: "Quicksand", sans-serif; color: var(--ink);
  }
  .ad > * { position: absolute; margin: 0; }

  .band { left: 0; top: 840px; width: 1200px; height: 120px; background: var(--band); }

  .photo {
    left: 555px; top: -405px; width: 950px; height: 950px; border-radius: 50%;
    background:
      radial-gradient(ellipse at 55% 62%, #8a5a44 0%, #b07a62 22%, rgba(200,170,150,0.6) 40%, rgba(200,220,230,0) 60%),
      linear-gradient(120deg, #2f7fc0 0%, #4a93cf 30%, #d9e4ea 60%, #eef3f6 100%);
  }

  .arcs { left: 530px; top: 220px; width: 220px; height: 170px; overflow: visible; }

  .tagline {
    left: 60px; top: 60px; font-family: "Playfair Display", serif; font-weight: 400;
    font-size: 37px; line-height: 1; color: var(--ink);
  }
  .headline { left: 60px; top: 110px; font-weight: 700; font-size: 60px; line-height: 76px; letter-spacing: 0.5px; }
  .headline .line-teal { color: var(--teal); display: block; }
  .headline .line-green { color: var(--green); display: block; }
  .rule { left: 60px; top: 273px; width: 303px; height: 6px; background: var(--green); }

  .intro { left: 60px; top: 322px; font-weight: 500; font-size: 32px; line-height: 43px; letter-spacing: 0.3px; }

  .requirements-label {
    left: 332px; top: 531px; width: 326px; height: 58px; border: 3px solid var(--teal);
    border-radius: 34px; display: flex; align-items: center; justify-content: center;
    font-weight: 500; font-size: 32px; letter-spacing: 0.5px;
  }
  .requirements { list-style: none; padding: 0; font-weight: 500; font-size: 32px; letter-spacing: 0.5px; }
  .requirements li { position: relative; padding-left: 28px; height: 59px; line-height: 40px; }
  .requirements li::before { content: "+"; position: absolute; left: 0; color: var(--green); font-weight: 600; }
  .req-left { left: 358px; top: 603px; }
  .req-right { left: 700px; top: 603px; }
  .req-right li.wrap { line-height: 48px; height: auto; top: -4px; }

  .benefits {
    left: -21px; top: 567px; width: 326px; height: 326px; border-radius: 50%;
    background: var(--green); color: var(--white);
  }
  .benefits-text {
    position: absolute; left: 30px; top: 80px; width: 260px;
    transform: rotate(-10deg); transform-origin: 50% 50%;
    font-weight: 600; font-size: 26px; line-height: 37px; text-align: center;
  }
  .benefits-text strong { font-weight: 700; font-size: 27px; display: block; }

  .url {
    left: 318px; top: 869px; width: 586px; height: 62px; border-radius: 31px;
    background: var(--teal); color: var(--white); display: flex; align-items: center;
    justify-content: center; font-family: "Playfair Display", serif; font-size: 34px;
  }

  .brand {
    left: 940px; top: 718px; width: 212px; height: 212px; border-radius: 50%;
    background: var(--white); border: 3px solid var(--ring);
    display: flex; flex-direction: column; align-items: center; justify-content: center; gap: 14px;
  }
  .brand-dot { width: 44px; height: 44px; border-radius: 50%; background: var(--teal); }
  .brand-name { font-weight: 700; font-size: 22px; color: var(--ink); text-align: center; line-height: 1.15; }
</style>
</head>
<body>
<main class="ad">
  <div class="band"></div>
  <div class="photo" role="img" aria-label="Foto: Pflegekräfte legen im Team ihre Hände übereinander"></div>

  <svg class="arcs" viewBox="0 0 220 170" aria-hidden="true">
    <path d="M17 98 C 20 40, 60 5, 130 10 S 180 15, 190 22" fill="none" stroke="var(--teal)" stroke-width="6" stroke-linecap="round"/>
    <path d="M45 157 C 48 90, 70 52, 120 47 S 195 55, 193 63" fill="none" stroke="var(--green)" stroke-width="6" stroke-linecap="round"/>
  </svg>

  <p class="tagline">Pflege mit Herz &amp; Seele</p>
  <h1 class="headline">
    <span class="line-teal">Komm in unser</span>
    <span class="line-green">Team Pflege!</span>
  </h1>
  <div class="rule"></div>

  <p class="intro">Hilf uns die Pflege in der<br>Umgebung Dessau-Roßlau<br>qualitativ zu verbessern und<br>menschlicher zu gestalten.</p>

  <div class="requirements-label">Das bringt du mit:</div>
  <ul class="requirements req-left">
    <li>Teamfähigkeit</li>
    <li>Hilfsbereitschaft</li>
    <li>Engagement</li>
  </ul>
  <ul class="requirements req-right">
    <li>Führerschein Klasse B</li>
    <li class="wrap">Gute Deutschkenntnisse<br>in Wort/Schrift</li>
  </ul>

  <div class="benefits">
    <p class="benefits-text">
      <strong>Wir garantieren:</strong>
      - 30 Tage Urlaub<br>
      - Fortbildungen<br>
      - TOP Vergütung<br>
      …
    </p>
  </div>

  <div class="url">www.lindenhof-pflege.de/karriere/</div>

  <div class="brand">
    <span class="brand-dot"></span>
    <span class="brand-name">LINDENHOF<br>PFLEGE</span>
  </div>
</main>
</body>
</html>
```